Local fast-growing company in the service sector

We are looking for a modern business card design, which should also appear on our letterheads

Target Market(s)

Private and industrial sectors

Contact Information for Business Card

Vorname Name
Kellberger Str. 18
71398 Lindenau
Tel.: 07146-839214-0
Name@agentur-kvtl.de

Colors
9d9d9d
919191
aaaaaa

Requirements
Must have
• The logo (file) in silver

```html
<!DOCTYPE html>
<html lang="de">
<head>
<meta charset="utf-8">
<title>KVTL – Visitenkarte</title>
<link rel="stylesheet" href="https://fonts.googleapis.com/css2?family=Open+Sans:wght@400;600;700&display=swap">
<style>
  :root {
    --backdrop: #3a342f;
    --card: #0d0d0d;
    --card-edge: #1c1c1c;
    --silver: #aaaaaa;
    --silver-mid: #9d9d9d;
    --silver-dark: #919191;
    --text-light: #e6e6e6;
    --divider: #262626;
  }
  * { margin: 0; padding: 0; box-sizing: border-box; }
  html, body {
    width: 1200px;
    height: 900px;
    overflow: hidden;
    background: var(--backdrop);
    font-family: "Open Sans", Arial, sans-serif;
  }
  .canvas {
    position: relative;
    width: 1200px;
    height: 900px;
    display: flex;
    align-items: center;
    justify-content: center;
    gap: 60px;
  }
  .card {
    position: relative;
    width: 520px;
    height: 338px;
    background: var(--card);
    border: 1px solid var(--card-edge);
    box-shadow: 0 18px 40px rgba(0, 0, 0, 0.55);
  }

  /* Front: brand left, contact right */
  .card-front { display: flex; }
  .brand-panel {
    width: 50%;
    display: flex;
    align-items: center;
    justify-content: center;
    gap: 14px;
  }
  .brand-square {
    width: 26px;
    height: 26px;
    background: var(--silver);
  }
  .brand-name {
    font-size: 54px;
    font-weight: 700;
    color: var(--silver);
    letter-spacing: 1px;
  }
  .contact-panel {
    width: 50%;
    border-left: 1px solid var(--divider);
    padding: 70px 0 0 34px;
    color: var(--text-light);
  }
  .person-name {
    font-size: 18px;
    font-weight: 700;
    color: var(--silver-dark);
    margin-bottom: 16px;
  }
  .address {
    font-style: normal;
    font-size: 14px;
    line-height: 1.45;
    margin-bottom: 22px;
  }
  .contact-list { list-style: none; font-size: 14px; line-height: 1.55; }
  .contact-list li { display: flex; align-items: center; gap: 10px; }
  .contact-icon { width: 11px; height: 11px; fill: var(--silver); flex: none; }

  /* Back: centered brand */
  .card-back {
    display: flex;
    align-items: center;
    justify-content: center;
    gap: 18px;
  }
  .card-back .brand-square { width: 30px; height: 30px; background: var(--silver-mid); }
  .card-back .brand-name { font-size: 64px; color: var(--silver-mid); }
</style>
</head>
<body>
<main class="canvas">
  <section class="card card-front">
    <div class="brand-panel">
      <span class="brand-square"></span>
      <span class="brand-name">KVTL</span>
    </div>
    <div class="contact-panel">
      <p class="person-name">Vorname Name</p>
      <address class="address">Kellberger Str. 18<br>71398 Lindenau</address>
      <ul class="contact-list">
        <li>
          <svg class="contact-icon" viewBox="0 0 12 12" aria-hidden="true"><path d="M2.5 0.8l2 2.2-1 1.3c.7 1.6 1.8 2.7 3.3 3.4l1.3-1 2.2 2-1.2 1.9C5.3 10.3 1.8 6.9 0.6 2z"/></svg>
          07146-839214-0
        </li>
        <li>
          <svg class="contact-icon" viewBox="0 0 12 12" aria-hidden="true"><path d="M0 2h12v1.2L6 7 0 3.2z M0 4.6l6 3.8 6-3.8V10H0z"/></svg>
          Name@agentur-kvtl.de
        </li>
        <li>
          <svg class="contact-icon" viewBox="0 0 12 12" aria-hidden="true"><circle cx="6" cy="6" r="6"/></svg>
          www.agentur-kvtl.de
        </li>
      </ul>
    </div>
  </section>

  <section class="card card-back">
    <span class="brand-square"></span>
    <span class="brand-name">KVTL</span>
  </section>
</main>
</body>
</html>
```